Fenlow Systems

Looking for a web site design to market our services/applications
We write and supply bespoke web applications for the offshore and construction industries
Our initial product is Tolv - rope access equipment management
Our buyers will be Rope Access companies via trade associations such as KOBEN and DULMO
we have a logo designed see it attached we would like to see crisp professional designs based around these colours and design
we will supply web copy later
looking for home, services, blog, contact us, order and a general template (privacy, site map, T&C) pages
Updates
This payment will be for the homepage only
We can discuss other options (pages) with the successful designer
Regards
Marcus
Industry/Entity Type
Construction
Look and feel
Each slider illustrates characteristics of the customer's brand and the style your logo design should communicate.

```html
<!DOCTYPE html>
<html lang="en">
<head>
<meta charset="utf-8">
<title>Fenlow Systems – Home</title>
<link href="https://fonts.googleapis.com/css2?family=Open+Sans:wght@400;600;700&display=swap" rel="stylesheet">
<style>
:root{
  --brand:#1e8fd8;
  --brand-dark:#1466a8;
  --ink:#2f2f2f;
  --muted:#6d6d6d;
  --band:#f1f1f1;
  --line:#e2e2e2;
  --badge:#d4d8de;
  --footer:#2a2a2a;
  --white:#ffffff;
}
*{box-sizing:border-box;margin:0;padding:0}
html,body{width:758px;height:1200px;overflow:hidden;background:var(--white)}
body{font-family:"Open Sans",Arial,sans-serif;color:var(--ink)}
.page{width:758px;height:1200px;position:relative}

/* header */
.site-header{height:86px;display:flex;align-items:center;justify-content:space-between;padding:0 40px 0 74px}
.brand{display:flex;align-items:center;gap:10px}
.brand-mark{width:40px;height:40px;background:var(--brand)}
.brand-name{font-size:17px;line-height:19px;font-weight:600;color:var(--brand-dark)}
.main-nav{display:flex}
.main-nav a{font-size:12px;color:var(--ink);text-decoration:none;padding:0 11px;border-left:1px solid var(--line);line-height:14px}
.main-nav a:first-child{border-left:0}

/* hero */
.hero{position:relative;height:328px}
.hero-photo{position:absolute;inset:0;background:linear-gradient(160deg,#dfe6ee 0%,#aebdcb 35%,#6f8396 60%,#dde3ea 100%)}
.hero-caption{position:absolute;left:72px;top:154px;background:rgba(30,30,30,.72);color:var(--white);font-size:14px;padding:6px 12px}
.hero-arrow{position:absolute;top:152px;width:18px;height:24px;background:rgba(60,60,60,.7);display:flex;align-items:center;justify-content:center}
.hero-arrow.prev{left:0}
.hero-arrow.next{right:0}

/* intro */
.intro{height:152px;text-align:center;padding-top:18px}
.intro h1{font-size:20px;font-weight:400;color:var(--ink)}
.intro p{font-size:9px;line-height:14px;color:var(--muted);width:470px;margin:10px auto 0}
.btn{display:inline-block;margin-top:18px;background:var(--brand);color:var(--white);font-size:11px;padding:6px 14px;border-radius:2px;text-decoration:none}

/* services */
.services{height:192px;background:var(--band);padding-top:14px}
.section-title{font-size:19px;font-weight:400;text-align:center;color:var(--ink)}
.service-grid{display:flex;justify-content:space-between;padding:0 100px;margin-top:24px}
.service{width:165px}
.service h3{font-size:13px;font-weight:400;color:var(--ink)}
.service p{font-size:8.5px;line-height:13px;color:var(--muted);margin-top:6px}
.more{display:flex;align-items:center;gap:5px;margin-top:6px;font-size:9px;color:var(--brand)}
.more svg{width:11px;height:11px}

/* buyers */
.buyers{height:198px;padding-top:16px;text-align:center}
.buyers p{font-size:9px;line-height:14px;color:var(--muted);width:500px;margin:10px auto 0}
.badge-row{display:flex;justify-content:center;gap:40px;margin-top:18px}
.partner-badge{width:90px;height:50px;background:var(--badge);display:block}

/* blog */
.blog{height:210px;background:var(--band);padding-top:18px}
.post-grid{display:flex;justify-content:center;gap:34px;margin-top:22px}
.post{display:flex;gap:10px;width:260px}
.post-photo{width:88px;height:74px;flex:none;background:linear-gradient(135deg,#c9d6e2,#8ea6bc)}
.post h4{font-size:10.5px;font-weight:700;color:var(--ink)}
.post time{display:block;font-size:8.5px;color:var(--brand);margin-top:3px}
.post p{font-size:8.5px;line-height:12px;color:var(--muted);margin-top:4px}

/* footer */
.site-footer{position:absolute;left:0;right:0;bottom:0;height:34px;background:var(--footer);display:flex;align-items:center;justify-content:space-between;padding:0 74px}
.site-footer small{font-size:8px;color:#d0d0d0}
.social{display:flex;gap:6px}
.social span{width:9px;height:9px;border-radius:50%;background:#bdbdbd;display:block}
</style>
</head>
<body>
<div class="page">
  <header class="site-header">
    <div class="brand">
      <span class="brand-mark"></span>
      <span class="brand-name">Fenlow<br>Systems</span>
    </div>
    <nav class="main-nav">
      <a href="#">Home</a><a href="#">Services</a><a href="#">Blog</a><a href="#">Order</a><a href="#">Contact us</a>
    </nav>
  </header>

  <section class="hero">
    <div class="hero-photo" role="img" aria-label="Business team in shirts and hard hat reviewing construction plans around a table"></div>
    <div class="hero-caption">Proin gravida nibh vel velit auctor aliquet</div>
    <span class="hero-arrow prev"><svg width="8" height="10" viewBox="0 0 8 10"><path d="M6 1 2 5l4 4" fill="none" stroke="#fff" stroke-width="1.6"/></svg></span>
    <span class="hero-arrow next"><svg width="8" height="10" viewBox="0 0 8 10"><path d="M2 1l4 4-4 4" fill="none" stroke="#fff" stroke-width="1.6"/></svg></span>
  </section>

  <section class="intro">
    <h1>Welcome quis bibendum auctor, nisi elit consequat ipsum</h1>
    <p>Aenean sollicitudin, lorem quis bibendum auctor, nisi elit consequat ipsum, nec sagittis sem nibh id elit. Duis sed odio sit amet nibh vulputate cursus a sit amet mauris. Morbi accumsan ipsum velit.</p>
    <a class="btn" href="#">Read More</a>
  </section>

  <section class="services">
    <h2 class="section-title">Services</h2>
    <div class="service-grid">
      <article class="service">
        <h3>Proin gravida nibh auctor</h3>
        <p>Aenean sollicitudin, lorem quis bibendum auctor, nisi elit consequat ipsum, nec sagittis sem nibh id elit.</p>
        <span class="more">more <svg viewBox="0 0 12 12"><circle cx="6" cy="6" r="6" fill="var(--brand)"/><path d="M5 3.5 7.5 6 5 8.5" fill="none" stroke="#fff" stroke-width="1.4"/></svg></span>
      </article>
      <article class="service">
        <h3>Lorem gravida nibh auctor</h3>
        <p>Aenean sollicitudin, lorem quis bibendum auctor, nisi elit consequat ipsum, nec sagittis sem nibh id elit.</p>
        <span class="more">more <svg viewBox="0 0 12 12"><circle cx="6" cy="6" r="6" fill="var(--brand)"/><path d="M5 3.5 7.5 6 5 8.5" fill="none" stroke="#fff" stroke-width="1.4"/></svg></span>
      </article>
      <article class="service">
        <h3>Gravida nibh auctor lorm</h3>
        <p>Aenean sollicitudin, lorem quis bibendum auctor, nisi elit consequat ipsum, nec sagittis sem nibh id elit.</p>
        <span class="more">more <svg viewBox="0 0 12 12"><circle cx="6" cy="6" r="6" fill="var(--brand)"/><path d="M5 3.5 7.5 6 5 8.5" fill="none" stroke="#fff" stroke-width="1.4"/></svg></span>
      </article>
    </div>
  </section>

  <section class="buyers">
    <h2 class="section-title">Our buyers</h2>
    <p>Aenean sollicitudin, lorem quis bibendum auctor, nisi elit consequat ipsum, nec sagittis sem nibh id elit. Duis sed odio sit amet nibh vulputate cursus a sit amet mauris. Morbi accumsan ipsum velit.</p>
    <div class="badge-row">
      <span class="partner-badge" role="img" aria-label="KOBEN association badge"></span>
      <span class="partner-badge" role="img" aria-label="DULMO association badge"></span>
    </div>
  </section>

  <section class="blog">
    <h2 class="section-title">Blog</h2>
    <div class="post-grid">
      <article class="post">
        <div class="post-photo" role="img" aria-label="Engineers discussing a project on site"></div>
        <div>
          <h4>Lorem Ipsumin gravida nibh</h4>
          <time>Monday, 4th August 2014</time>
          <p>Aenean sollicitudin, lorem quis bibendum auctor, nisi elit consequat ipsum.</p>
        </div>
      </article>
      <article class="post">
        <div class="post-photo" role="img" aria-label="Hands reviewing printed plans and charts"></div>
        <div>
          <h4>Lorem Ipsumin gravida nibh</h4>
          <time>Monday, 4th August 2014</time>
          <p>Aenean sollicitudin, lorem quis bibendum auctor, nisi elit consequat ipsum.</p>
        </div>
      </article>
    </div>
  </section>

  <footer class="site-footer">
    <small>Copyright © 2014. All Rights Reserved | Privacy | Sitemap | T&amp;C</small>
    <div class="social"><span></span><span></span><span></span><span></span><span></span></div>
  </footer>
</div>
</body>
</html>
```